Business Card Design Project

I need a business card designed from scratch. I have an existing logo that I can upload in Illustrator for modification or redesign.

The Company is called Query Lanterns http://querylanterns.com.au and we provide Search Engine Optimization services to Australian businesses. The current logo signifies an increase in visitors, profits etc...

There are no restrictions as to the redesign - colours, style etc are all open to change.

Cards will be full colour and one sided printed at http://www.cardmoxel.com.au so check their requirements for file format and sizes etc.

I will expect all original files upon completion of project.

Target Market(s)

Any business with a web site looking to improve their search engine rankings

Industry/Entity Type

Business

Requirements
Must have
• I like modern, sleek designs. Clean, not fussy, uncluttered.

```html
<!DOCTYPE html>
<html lang="en">
<head>
<meta charset="utf-8">
<title>Query Lanterns – Business Card</title>
<link rel="stylesheet" href="https://fonts.googleapis.com/css2?family=Open+Sans:wght@400;600;700;800&display=swap">
<style>
  :root {
    --brand-blue: #1472b8;
    --ink: #3a3a3a;
    --card-white: #ffffff;
    --stage: #e9e7e4;
    --accent-yellow: #f2b91c;
  }
  * { margin: 0; padding: 0; box-sizing: border-box; }
  html, body { width: 1200px; height: 460px; overflow: hidden; }
  body {
    background: var(--stage);
    font-family: "Open Sans", Arial, sans-serif;
    position: relative;
  }
  .card {
    position: absolute;
    width: 542px;
    height: 308px;
    border-radius: 14px;
    overflow: hidden;
    box-shadow: 0 3px 8px rgba(0,0,0,0.25);
  }
  .card--front { left: 36px; top: 74px; background: var(--card-white); }
  .card--back { left: 622px; top: 76px; background: var(--brand-blue); }

  .brand {
    position: absolute;
    left: 42px; top: 40px;
    display: flex; align-items: center; gap: 12px;
  }
  .brand__dot {
    width: 16px; height: 16px; border-radius: 50%;
    background: var(--accent-yellow);
  }
  .brand__name {
    font-weight: 800; font-size: 34px; line-height: 1;
    color: var(--brand-blue);
    font-family: "Open Sans", Arial, sans-serif;
  }

  .contacts {
    position: absolute; top: 184px; left: 74px;
    display: grid; grid-template-columns: 118px auto;
    row-gap: 4px; column-gap: 0;
    font-size: 13.5px; color: var(--ink);
  }
  .contact { display: flex; align-items: center; gap: 6px; white-space: nowrap; }
  .contact svg { width: 10px; height: 10px; fill: var(--brand-blue); flex: none; }

  .name-band { position: absolute; left: 0; top: 214px; width: 542px; height: 54px; }
  .name-band svg { position: absolute; inset: 0; }
  .name-band__text {
    position: absolute; left: 0; width: 450px; top: 13px;
    text-align: center; color: #fff;
    font-size: 16px; font-weight: 700;
  }
  .name-band__title { font-size: 12.5px; font-weight: 400; }

  .address {
    position: absolute; left: 74px; top: 268px;
    font-size: 13.5px; color: var(--ink);
  }

  .back-brand {
    position: absolute; left: 0; right: 0; top: 118px;
    text-align: center;
    font-weight: 800; font-size: 36px; color: #fff; line-height: 1;
  }
  .back-url {
    position: absolute; left: 0; right: 0; top: 222px;
    text-align: center; color: #fff;
    font-size: 13.5px; letter-spacing: 0.8px;
  }
</style>
</head>
<body>
  <section class="card card--front" aria-label="Business card front">
    <div class="brand">
      <span class="brand__dot"></span>
      <span class="brand__name">Query Lanterns</span>
    </div>

    <div class="contacts">
      <div class="contact">
        <svg viewBox="0 0 10 10"><path d="M2 0h2l1 3-1.5 1a6 6 0 0 0 2.5 2.5L7 5l3 1v2c0 1-1 2-2 2A8 8 0 0 1 0 2c0-1 1-2 2-2z"/></svg>
        090 555 0142
      </div>
      <div class="contact">
        <svg viewBox="0 0 10 10"><rect x="0" y="1.5" width="10" height="7" rx="1"/><path d="M0.5 2l4.5 3.5L9.5 2" stroke="#fff" stroke-width="1" fill="none"/></svg>
        enquiry@querylanterns.com.au
      </div>
      <div class="contact">
        <svg viewBox="0 0 10 10"><rect x="2" y="0" width="6" height="10" rx="1.2"/><rect x="3" y="1.5" width="4" height="5.5" fill="#fff"/></svg>
        090 555 0142
      </div>
      <div class="contact">
        <svg viewBox="0 0 10 10"><circle cx="5" cy="5" r="4.5"/></svg>
        www.querylanterns.com.au
      </div>
    </div>

    <div class="name-band">
      <svg viewBox="0 0 542 54" width="542" height="54" aria-hidden="true">
        <path d="M0 20 Q0 10 14 10 L470 10 Q508 10 520 2 L542 0 L542 28 Q538 40 518 42 L60 42 Q18 42 6 52 L0 54 Z" fill="var(--brand-blue)"/>
      </svg>
      <div class="name-band__text">Your Name <span class="name-band__title">Title</span></div>
    </div>

    <div class="address">00Floor Street, City Name State Name, Contry Name</div>
  </section>

  <section class="card card--back" aria-label="Business card back">
    <div class="back-brand">Query Lanterns</div>
    <div class="back-url">www.querylanterns.com.au</div>
  </section>
</body>
</html>
```